Business Card - high end, modern health care

Hey designers!

We need a double sided business card for the boutique, cutting edge physical therapy rehabilitation centre in Sydney's Northern Beaches.

With the most qualified physios in the area The Harbourview Motion Clinic does what other physiotherapy practices do not, we take our time with our patients giving them longer appointments, better physios and therefor faster results!

We guarantee that the service people receive at THMC will be unparalleled.

Hence we need a business card to reflect our modern, boutique, high end service. The final design needs to reflect that we are in a class of our own yet with the feel of beachside retreat.

Below I have attached our logo in both blue on white and white on blue. The exact colour is;
and the font that we have used in our logo is Tex Gyre Aventador.

I like the idea of the blue as the main colour as it is more eye catching and our signage onto the main road will be in this blue and in the interest of consistency across marketing the blue needs to be a part of the design. However I would appreciate a few designs onto a wooden background as this is a visual theme within the fitout of the practice.

The design needs to be of standard size (91x55mm).

Target Market(s)

We target people who have an end outcome in mind and those who have had poor experiences with other providers and ensure that everyone gets the care that they deserve with a premium service that is tailored to the individuals circumstances. As a premium service, the target market is highly educated, business and tech savvy with the additional target market of elderly people who have self funded their retirement and see value in paying for the best ongoing rehabilitation to maintain independence.

Industry/Entity Type

Physical Therapy

Contact Information for Business Card

Name, designation( Titled Musculoskeletal Physiotherapist... there will also be those in the company that have multiple designations ie 5 or 6 words long), phone number, email, facebook, instagram, address

Font styles to use
Sans Serif

Colors

Designer to choose colors to be used in the design.

Requirements
Must have
• Front - The logo as large as possible, blue or wooden theme, and all of the important details.
• Back - A blank space/lines on which to write appointment times (no "Appointment, date, time" etc.)
Nice to have
• facebook url
• logos for facebook and instagram
• Mini logos for the phone and email?

```html
<!DOCTYPE html>
<html lang="en">
<head>
<meta charset="utf-8">
<title>The Harbourview Motion Clinic – Business Card</title>
<link rel="stylesheet" href="https://fonts.googleapis.com/css2?family=Raleway:wght@400;500;600&display=swap">
<style>
  :root {
    --brand-blue: #0d58a8;
    --ink: #1a1a1a;
    --muted: #333333;
    --rule: #6b6b6b;
    --paper: #ffffff;
    --backdrop: #56627a;
    --social-a: #1e8fd6;
    --social-b: #e05a9b;
  }
  * { box-sizing: border-box; margin: 0; padding: 0; }
  html, body {
    width: 1200px; height: 1000px; overflow: hidden;
    background: var(--backdrop);
    font-family: "Raleway", Arial, sans-serif;
  }
  .canvas { position: relative; width: 1200px; height: 1000px; }

  .card { position: absolute; width: 658px; height: 376px; }

  /* Front */
  .card--front { left: 136px; top: 78px; background: var(--brand-blue); }
  .front__mark { position: absolute; left: 207px; top: 164px; }
  .card--front .front__mark { left: 71px; top: 86px; }
  .front__name {
    position: absolute; left: 316px; top: 166px;
    color: var(--paper); font-weight: 600; text-transform: uppercase;
    line-height: 1.1;
  }
  .front__name-line1 { display: block; font-size: 25px; letter-spacing: 0.5px; }
  .front__name-line2 { display: block; font-size: 15px; letter-spacing: 4.2px; margin-top: 3px; }

  /* Back */
  .card--back { left: 437px; top: 548px; background: var(--paper); }
  .back__spine {
    position: absolute; left: 0; top: 0; width: 126px; height: 100%;
    border-right: 1px solid var(--ink);
  }
  .back__brand {
    position: absolute; left: 63px; top: 188px;
    transform: translate(-50%, -50%) rotate(-90deg);
    display: flex; align-items: center; gap: 10px;
    color: var(--brand-blue); font-weight: 600; text-transform: uppercase;
    white-space: nowrap; line-height: 1.05;
  }
  .back__brand-dot { width: 34px; height: 34px; border-radius: 50%; background: var(--brand-blue); flex: none; }
  .back__brand-text span { display: block; }
  .back__brand-line1 { font-size: 19px; }
  .back__brand-line2 { font-size: 15px; letter-spacing: 3px; }

  .person { position: absolute; left: 152px; top: 72px; }
  .person__name { font-size: 23px; font-weight: 500; color: var(--ink); }
  .person__name em { font-style: normal; color: var(--brand-blue); }
  .person__role { font-size: 14px; color: var(--muted); margin-top: 6px; }

  .rule { position: absolute; left: 126px; width: 478px; height: 1px; background: var(--ink); }
  .rule--top { top: 143px; }
  .rule--bottom { top: 287px; }

  .contact { position: absolute; left: 150px; display: flex; align-items: center; font-size: 17px; color: var(--ink); }
  .contact svg { width: 24px; height: 24px; margin-right: 16px; }
  .contact--phone { top: 170px; }
  .contact--email { top: 202px; }

  .social { position: absolute; top: 252px; display: flex; align-items: center; font-size: 15px; color: var(--muted); }
  .social__dot { width: 20px; height: 20px; border-radius: 50%; margin-right: 10px; }
  .social--facebook { left: 152px; }
  .social--facebook .social__dot { background: var(--social-a); }
  .social--instagram { left: 378px; }
  .social--instagram .social__dot { background: var(--social-b); margin-right: 16px; }

  .appointment-line {
    position: absolute; left: 157px; top: 337px; width: 448px;
    border-top: 1px dashed var(--rule);
  }
</style>
</head>
<body>
<main class="canvas">

  <section class="card card--front" aria-label="Card front">
    <svg class="front__mark" width="198" height="198" viewBox="0 0 198 198" aria-hidden="true">
      <circle cx="99" cy="99" r="92" fill="none" stroke="var(--paper)" stroke-width="14"/>
    </svg>
    <div class="front__name">
      <span class="front__name-line1">The Harbourview</span>
      <span class="front__name-line2">Motion Clinic</span>
    </div>
  </section>

  <section class="card card--back" aria-label="Card back">
    <div class="back__spine">
      <div class="back__brand">
        <span class="back__brand-dot"></span>
        <div class="back__brand-text">
          <span class="back__brand-line1">The Harbourview</span>
          <span class="back__brand-line2">Motion Clinic</span>
        </div>
      </div>
    </div>

    <div class="person">
      <p class="person__name">Name of <em>Person</em></p>
      <p class="person__role">Designation</p>
    </div>

    <div class="rule rule--top"></div>

    <p class="contact contact--phone">
      <svg viewBox="0 0 24 24" aria-hidden="true">
        <circle cx="12" cy="12" r="10.5" fill="none" stroke="var(--ink)" stroke-width="1.6"/>
        <path d="M8.2 6.8c.5-.4 1.1-.3 1.4.2l1 1.7c.3.5.1 1-.3 1.3l-.6.4c.5 1.3 1.5 2.4 2.8 3l.4-.6c.3-.4.9-.6 1.3-.3l1.7 1c.5.3.6.9.2 1.4l-.6.7c-.6.6-1.5.8-2.3.5-2.8-1.1-4.9-3.2-5.9-6-.3-.8-.1-1.7.5-2.3z" fill="var(--ink)"/>
      </svg>
      612.555.0148
    </p>
    <p class="contact contact--email">
      <svg viewBox="0 0 24 24" aria-hidden="true">
        <rect x="1" y="5" width="22" height="14" fill="var(--ink)"/>
        <path d="M1.5 5.5 12 13l10.5-7.5" fill="none" stroke="var(--paper)" stroke-width="1.4"/>
      </svg>
      reception@thmc-mail.com
    </p>

    <p class="social social--facebook"><span class="social__dot"></span>facebook/name</p>
    <p class="social social--instagram"><span class="social__dot"></span>instagram_name</p>

    <div class="rule rule--bottom"></div>
    <div class="appointment-line"></div>
  </section>

</main>
</body>
</html>
```